Harborview Estates Business Card for Apartment Buildings

Create business cards for resident managers who run apartment buildings. The audience is the public who are searching for apartment rentals, and current residents who live at the apartment building. Key design element will be incorporating the company logo, however, the logo cannot dominate. The building name and manager name are more important than the logo. Current business card design leaves little room for copy, so we may need to reduce the size on the current card to allow for more space for copy.

Target Market(s)

Adults 18-65 years of age, who are looking for an apartment rental, plus current residents who live at our apartment buildings.

Industry/Entity Type

Property Management

Contact Information for Business Card

A major design element will be use of the company logo. Important property and manager contact information must be part of the design. The size of the logo will need to be reduced to make room for building and manager contact copy.

Font styles to use
Sans Serif

Colors
3176b5
000000
959595
ffffff

Requirements
Must have
• 1) Incorporate the company logo.
• 2) Use the company colors (dark blue, black/grey, over white).
• 3) FEATURE THE BUILDING NAME
• 4) FEATURE THE MANAGER NAME
• 5) The company name is less important than BUILDING and MANAGER
• 6) Manager contact information
• **SEE ATTACHED CREATIVE BRIEF**
Nice to have
• 1) Back of card logo watermark
• 2) Ability to write notes on back of carfd
Should not have
• Avoid letting the company logo dominate the card, the building name and manager are more important than the company logo.

```html
<!DOCTYPE html>
<html lang="en">
<head>
<meta charset="utf-8">
<title>Harborview Estates – Resident Manager Business Card</title>
<link rel="stylesheet" href="https://fonts.googleapis.com/css2?family=Roboto:wght@400;500;700&display=swap">
<style>
  :root {
    --brand-blue: #1b68a8;
    --ink-grey: #4a4a4c;
    --rule-grey: #959595;
    --card-white: #f4f4f4;
    --backdrop: #2b2b2b;
    --watermark: rgba(27, 104, 168, 0.07);
  }
  * { box-sizing: border-box; margin: 0; padding: 0; }
  html, body {
    width: 1200px; height: 960px; overflow: hidden;
    background: var(--backdrop);
    font-family: "Roboto", Arial, sans-serif;
  }
  .canvas { position: relative; width: 1200px; height: 960px; }
  .card {
    position: absolute; width: 600px; height: 342px;
    background: var(--card-white); overflow: hidden;
  }
  .card--front { left: 314px; top: 113px; }
  .card--back { left: 311px; top: 472px; }

  /* Front */
  .building-name {
    position: absolute; right: 36px; top: 18px;
    font-size: 42px; font-weight: 700; color: var(--brand-blue);
    letter-spacing: 0.2px; white-space: nowrap;
  }
  .address {
    position: absolute; right: 8px; top: 87px;
    text-align: right; font-size: 15px; line-height: 19px; color: var(--ink-grey);
  }
  .manager {
    position: absolute; right: 36px; top: 148px; text-align: right;
  }
  .manager__name { font-size: 22px; font-weight: 500; color: var(--brand-blue); line-height: 26px; }
  .manager__role { font-size: 15px; font-weight: 500; color: var(--ink-grey); line-height: 20px; }
  .contact-list {
    position: absolute; right: 36px; top: 219px; list-style: none;
  }
  .contact-list li {
    display: flex; justify-content: flex-end; align-items: center;
    height: 19.2px; font-size: 14.5px; color: var(--ink-grey);
  }
  .contact-list svg { width: 14px; height: 14px; margin-left: 8px; fill: var(--brand-blue); }
  .company-mark {
    position: absolute; left: 44px; top: 150px;
    display: flex; align-items: center; gap: 14px;
  }
  .company-mark__dot { width: 22px; height: 22px; border-radius: 50%; background: var(--brand-blue); }
  .company-mark__name {
    font-size: 30px; font-weight: 700; line-height: 34px; color: var(--brand-blue);
  }

  /* Back */
  .back-mark {
    position: absolute; left: 40px; top: 58px;
    display: flex; align-items: center; gap: 10px;
  }
  .back-mark__square { width: 18px; height: 18px; background: var(--brand-blue); }
  .back-mark__name { font-size: 26px; font-weight: 700; color: var(--brand-blue); letter-spacing: 0.5px; }
  .back-watermark {
    position: absolute; left: 150px; top: 120px;
    font-size: 60px; font-weight: 700; line-height: 68px; color: var(--watermark);
    white-space: nowrap;
  }
  .note-lines { position: absolute; left: 39px; top: 152px; width: 521px; }
  .note-lines span {
    display: block; height: 30.6px; border-bottom: 1.5px solid var(--rule-grey);
  }
  .note-lines span:first-child { height: 0; }
</style>
</head>
<body>
<main class="canvas">
  <section class="card card--front" aria-label="Business card front">
    <div class="company-mark">
      <span class="company-mark__dot"></span>
      <span class="company-mark__name">Harborview<br>Estates</span>
    </div>
    <h1 class="building-name">Cedar Court Apartments</h1>
    <p class="address" style="right:36px">1458 Larkspur Avenue<br>Brookfield, CA 90000</p>
    <div class="manager">
      <p class="manager__name">Marisol Delgado</p>
      <p class="manager__role">Resident Manager</p>
    </div>
    <ul class="contact-list">
      <li>555-210-4418
        <svg viewBox="0 0 16 16" aria-hidden="true"><path d="M3.6 1.2l2.3 2.6-1.2 1.9c.9 2 2.6 3.7 4.6 4.6l1.9-1.2 2.6 2.3-1.3 2.6C7.3 13.7 2.3 8.7 1 3.5z"/></svg>
      </li>
      <li>555-318-7702
        <svg viewBox="0 0 16 16" aria-hidden="true"><path d="M4.5 1h7v14h-7zM5.8 2.5v9.5h4.4V2.5z"/><circle cx="8" cy="13.5" r=".8" fill="#f4f4f4"/></svg>
      </li>
      <li>555-640-1195
        <svg viewBox="0 0 16 16" aria-hidden="true"><path d="M4 1h8v4H4zM1 6h14v6h-2.5v-2h-9v2H1zM4.5 11h7v4h-7z"/></svg>
      </li>
      <li>marisol@harborviewest.com
        <svg viewBox="0 0 16 16" aria-hidden="true"><path d="M1 3.5h14v9H1zM2.5 5v.3L8 9l5.5-3.7V5L8 8.6z"/></svg>
      </li>
      <li>www.harborviewest.com
        <svg viewBox="0 0 16 16" aria-hidden="true"><circle cx="8" cy="8" r="7"/><path d="M4 5c2 0 2 2 3.5 2S9 10 7 11 5 13 5 13 3 9 4 5zM10 3c1 1 3 2 2 4s-2 0-2-1-1-2 0-3z" fill="#f4f4f4"/></svg>
      </li>
    </ul>
  </section>

  <section class="card card--back" aria-label="Business card back">
    <div class="back-watermark" aria-hidden="true">Harborview<br>Estates</div>
    <div class="back-mark">
      <span class="back-mark__square"></span>
      <span class="back-mark__name">HARBORVIEW ESTATES</span>
    </div>
    <div class="note-lines" aria-label="Lines for notes">
      <span></span><span></span><span></span><span></span><span></span><span></span>
    </div>
  </section>
</main>
</body>
</html>
```